Auto Body Shops Needs Email Signature Design

We are looking to update our email signature. The design needs to be easy to copy and paste into Microsoft Outlook and be editable for multiple positions.

Our company is called Dellwyn Collision & Autoglass, but we have a charity program called Dellwyn Helps Young Ones. We would like to use this logo.

Information that needs to be included:

"We Care"
Name
Title
Location
Address
Phone
Email
Cell
Fax

Our new corporate colors are gray/silver and black. We are getting away from blue (currently used).

The "Dellwyn" and "Helps Young" should be in black as they will be on a white background (comp screen).

Colors
fde1e1

Requirements
Must have
• Easily editable so it can be used as a template.
Should not have
• Main color should not be red.

```html
<!DOCTYPE html>
<html lang="en">
<head>
<meta charset="utf-8">
<title>Dellwyn Email Signature</title>
<link rel="stylesheet" href="https://fonts.googleapis.com/css2?family=Catamaran:wght@400;500;700&family=Merriweather:wght@400&family=Arimo:wght@400&display=swap">
<style>
  :root {
    --ink: #111111;
    --band: #0d0d0d;
    --paper: #ffffff;
    --silver: #9aa0a6;
    --frame: #222222;
    --link-red: #a4160f;
  }
  html, body {
    margin: 0;
    padding: 0;
    width: 1200px;
    height: 960px;
    overflow: hidden;
    background: var(--paper);
  }
  .signature {
    position: relative;
    width: 1200px;
    height: 960px;
    font-family: "Catamaran", sans-serif;
    color: var(--ink);
  }
  .care-band {
    position: absolute;
    left: 18px;
    top: 325px;
    width: 1160px;
    height: 74px;
    background: var(--band);
  }
  .care-title {
    position: absolute;
    left: 32px;
    top: 12px;
    margin: 0;
    font-family: "Merriweather", serif;
    font-weight: 400;
    font-size: 42px;
    line-height: 1.1;
    color: var(--paper);
  }
  .charity-box {
    position: absolute;
    left: 18px;
    top: 398px;
    width: 428px;
    height: 169px;
    border: 2px solid var(--frame);
    display: flex;
    align-items: center;
    justify-content: center;
    gap: 10px;
  }
  .charity-dot {
    width: 14px;
    height: 14px;
    border-radius: 50%;
    background: var(--link-red);
  }
  .charity-name {
    font-weight: 700;
    font-size: 29px;
    color: var(--ink);
    line-height: 1;
  }
  .contact-line {
    position: absolute;
    left: 471px;
    margin: 0;
    white-space: nowrap;
    line-height: 34px;
  }
  .identity { top: 427px; font-size: 23px; color: var(--silver); }
  .person-name { font-size: 29px; font-weight: 700; color: var(--ink); }
  .sep { margin: 0 5px; }
  .email { font-size: 25px; color: var(--ink); text-decoration: underline; margin-left: 6px; font-weight: 500; }
  .phone { font-size: 27px; }
  .phone-cell { top: 463px; }
  .phone-fax { top: 492px; }
  .phone .label { color: var(--ink); }
  .phone .number { color: var(--silver); }
  .web {
    top: 538px;
    font-size: 23px;
    line-height: 30px;
    font-weight: 700;
    color: var(--link-red);
  }
  .disclaimer {
    position: absolute;
    left: 18px;
    top: 592px;
    width: 1182px;
    margin: 0;
    font-family: "Arimo", sans-serif;
    font-size: 15.5px;
    line-height: 18.5px;
    color: var(--ink);
    white-space: nowrap;
  }
</style>
</head>
<body>
<main class="signature">
  <header class="care-band">
    <h1 class="care-title">We Care</h1>
  </header>

  <section class="charity-box" aria-label="Dellwyn Helps Young Ones">
    <span class="charity-dot"></span>
    <span class="charity-name">Dellwyn Helps Young Ones</span>
  </section>

  <p class="contact-line identity">
    <span class="person-name">First Last</span><span class="sep">|</span>Regional Manager<span class="sep">|</span>H.O. Ashbury<span class="sep">|</span><span class="email">email@dellwyn.com</span>
  </p>
  <p class="contact-line phone phone-cell"><span class="label">Cell:</span> <span class="number">555-201-4830</span></p>
  <p class="contact-line phone phone-fax"><span class="label">Fax:</span> <span class="number">555-201-4831</span></p>
  <p class="contact-line web">http://www.dellwyn.com/dellwyn</p>

  <p class="disclaimer">This e-mail and any attachments may contain confidential information.&nbsp; It is intended for the addressee(s) names herein.&nbsp; If you are not the intended recipient of this<br>e-mail you are notified that any dissemination, distribution or duplication of this email and attachments is strictly prohibited. If you received this e-mail in error, please<br>notify me immediately and permanently delete / dispose of the original and any copy of the email, attachments or printed copies.</p>
</main>
</body>
</html>
```